We’re a real estate firm that has landed a big builder in a neighboring state. Our branding needs...

We are a real estate firm who represents various builders along with doing resale here in Oregon. Our firm is growing to represent a big builder in Washington State and we’ll have another 40 brokers on our team. We need rebranding. As in, a new logo ( the house logo we have now looks cartoonish, hate it). We need new cards, something to really stand out. I’ve been thinking of using those NFC cards from ZEP or the ones with the seam color. I likely want two or three designs, a darker (as in a background color of black or grey) , a light one ( again I mean background color) and a credit card style (either plastic w an embossed name/number on front, or metal ). I’m thinking dark background for cc, or silver if it’s metal. That’s my thoughts, but you are the artists, so maybe you have an idea I haven’t considered. Our colors were black and red, but we don’t have to stick to that. Just nothing too busy. Oh, and we are typically representing the local, higher quality builders in our area (just below custom), but not national. Subdivisions are near the Kell Varney, Brisco, and Thornfield Crest sites. We are super excited, but without a lot of time to change the “look” of our brokerage. So I’ll be deciding and moving forward within 24 hours tops. Our name is Real Estate Summit Alliance ( we cant change the name because of timeline and business license) Thank you!

Industry/Entity Type

Real Estate

Contact Information for Business Card

The usual. Name of firm. Name of cardholder. Contact info.

Font styles to use
Serif
Sans Serif

Colors

Designer to choose colors to be used in the design.

Requirements
Must have
• A sleek or simple look. I included photos of cards with stylistic attributes we like. Thank you
Nice to have
• We really like the black backgrounds. With foil or embossed detail. We also like the black on black. Matte black card with raised shiny black detail. But still eye catching.
Should not have
• No ornate or busy looking style. We don’t want anything cluttered.

```html
<!DOCTYPE html>
<html lang="en">
<head>
<meta charset="utf-8">
<title>Real Estate Summit Alliance – Business Card</title>
<link rel="stylesheet" href="https://fonts.googleapis.com/css2?family=Lato:wght@400;700;900&display=swap">
<style>
  :root {
    --stage: #3b3b3d;
    --brand-red: #c8161d;
    --red-deep: #b51319;
    --card-white: #ffffff;
    --ink: #1f1f1f;
    --rule: #d9d9d9;
  }
  * { box-sizing: border-box; margin: 0; padding: 0; }
  html, body { width: 1200px; height: 782px; overflow: hidden; }
  body {
    background: var(--stage);
    font-family: "Lato", sans-serif;
    display: flex;
    align-items: center;
    justify-content: center;
    gap: 40px;
  }
  .card {
    width: 540px;
    height: 309px;
    position: relative;
    box-shadow: 0 8px 22px rgba(0,0,0,.45);
    overflow: hidden;
  }

  /* Front */
  .card--front { background: var(--card-white); color: var(--ink); }
  .brand-block {
    position: absolute;
    left: 34px;
    top: 0;
    height: 100%;
    width: 220px;
    display: flex;
    align-items: center;
  }
  .brand-name {
    color: var(--brand-red);
    font-weight: 900;
    font-size: 22px;
    line-height: 1.15;
    letter-spacing: .5px;
    text-transform: uppercase;
  }
  .divider {
    position: absolute;
    left: 268px;
    top: 62px;
    width: 1px;
    height: 185px;
    background: var(--rule);
  }
  .contact-block {
    position: absolute;
    left: 290px;
    top: 72px;
    right: 20px;
  }
  .holder-name {
    color: var(--brand-red);
    font-weight: 700;
    font-size: 19px;
    letter-spacing: 1px;
    text-transform: uppercase;
    line-height: 1.1;
  }
  .holder-title { font-size: 13px; margin-bottom: 6px; }
  .contact-list { list-style: none; font-size: 13.5px; line-height: 1.38; }
  .contact-list li { display: flex; align-items: center; gap: 6px; }
  .contact-list svg { width: 11px; height: 11px; fill: var(--brand-red); flex: none; }
  .address { font-size: 13.5px; line-height: 1.38; margin-top: 2px; }

  /* Back */
  .card--back { background: var(--brand-red); }
  .back-texture {
    position: absolute;
    inset: 0;
    background: linear-gradient(135deg, var(--brand-red), var(--red-deep));
  }
  .back-name {
    position: absolute;
    left: 300px;
    top: 148px;
    color: #ffffff;
    font-weight: 900;
    font-size: 32px;
    letter-spacing: 1px;
  }
</style>
</head>
<body>

  <section class="card card--front" aria-label="Business card front">
    <div class="brand-block">
      <p class="brand-name">Real Estate<br>Summit Alliance</p>
    </div>
    <div class="divider"></div>
    <div class="contact-block">
      <h1 class="holder-name">Marcus Dell</h1>
      <p class="holder-title">Managing Director</p>
      <ul class="contact-list">
        <li>
          <svg viewBox="0 0 12 12" aria-hidden="true"><path d="M1 3c0-1 1-2 5-2s5 1 5 2v1H8V3H4v1H1z M2 5h8l1 6H1z"/></svg>
          503-555 0142
        </li>
        <li>
          <svg viewBox="0 0 12 12" aria-hidden="true"><path d="M3 0h6v12H3z M4 1v9h4V1z"/></svg>
          503-555 0142
        </li>
        <li>
          <svg viewBox="0 0 12 12" aria-hidden="true"><path d="M0 2h12v8H0z M1 3l5 4 5-4z" fill-rule="evenodd"/></svg>
          hello@summitalliance.test
        </li>
        <li>
          <svg viewBox="0 0 12 12" aria-hidden="true"><circle cx="6" cy="6" r="6"/></svg>
          www.summitalliance.test
        </li>
      </ul>
      <p class="address">410 Ridgeline Way, Suite 2<br>Portland, OR 97201.</p>
    </div>
  </section>

  <section class="card card--back" aria-label="Business card back">
    <div class="back-texture" role="img" aria-label="Tonal red repeating brand-name pattern"></div>
    <p class="back-name">RESA</p>
  </section>

</body>
</html>
```